Scrum Master & Agile IT Coach Needing Business Website

Hello, my name is Joel Brandt
I am a project manger, scrum master, & agile coach. I work with IT development teams on major projects for Summit 300 companies . My project management business has a website and can be found here: www.tk-steadfast.example

I have launched a new company, ALL focused on IT Agile Coaching, I am looking to have a website created for my new company - the name of the new company is: Q's and V's - Agile IT Coaching and Training.
I have a logo and it is provided in the materials. I like to logo; I am open to different color pallets.

The website will have a total of 7 pages; I have content for 5 of the 7 pages prepared; the other 2 pages will say under construction.

Page 1 Who am I, What I do, My Experience
Demonstrated experience and progression from Scrum Master to
Program Manager to Coach

Page 2 Q's & V's - Agile Team Coaching
teams working major IT projects, multiple months/years

Page 3 Coaching @ the Team Level

Page 4 Coaching @ the Program Level ; LIMBr ART level

Pages 5 -6 Under Construction

Page 7 Presentations, Slide Decks, Reference Materials

Mentors Nook need to have this highlighted somewhere Monthly Blog
Updates

Industry/Entity Type

IT development

Coding

Coded - Design and coding required

Number of Pages Required

5+ page

Requirements
Must have
• the website must be bold - I want those who visit to remember coming to my coaching site
Nice to have
• nice to have will be a modern / futuristic website; I work with IT developers, I want a website they will like
Should not have
• should not be stiff - it should be professional but fun

```html
<!DOCTYPE html>
<html lang="en">
<head>
<meta charset="utf-8">
<title>Q's &amp; V's - Agile IT Coaching and Training</title>
<link href="https://fonts.googleapis.com/css2?family=Outfit:wght@400;500;600;700;800&display=swap" rel="stylesheet">
<style>
:root{
  --blue:#1a72bf;
  --blue-deep:#15549e;
  --navy:#0d3f84;
  --navy-dark:#0b2d63;
  --nav-active:#114e96;
  --ink:#1b1b1b;
  --white:#fff;
  --black:#000;
}
*{box-sizing:border-box;margin:0;padding:0}
html,body{width:1200px;height:3014px;overflow:hidden}
body{position:relative;font-family:"Outfit",sans-serif;color:var(--ink);background:var(--white)}
.abs{position:absolute}
ul{list-style:none}

.brand{left:100px;top:38px;display:flex;align-items:center;gap:12px}
.brand-mark{width:40px;height:40px;background:var(--blue-deep);display:block}
.brand-name{font-size:42px;font-weight:800;color:var(--blue-deep);letter-spacing:1px}
.contact{top:48px;display:flex;gap:12px;align-items:center}
.contact .ico{width:36px;height:36px;background:var(--blue);border-radius:3px;display:flex;align-items:center;justify-content:center}
.contact b{display:block;color:var(--blue-deep);font-size:15px;font-weight:600}
.contact span{font-size:15px;color:var(--ink)}
.tools{left:950px;top:54px;display:flex;gap:12px}
.tools i{width:28px;height:28px;background:#e5e8ee;display:block}
.tools i.search{display:flex;align-items:center;justify-content:center}

.nav{left:0;top:133px;width:1200px;height:50px;background:var(--blue)}
.nav a{position:absolute;top:0;height:50px;line-height:50px;color:var(--white);font-size:16.5px;text-decoration:none;font-weight:500}
.nav a.active{background:var(--nav-active);padding:0 11px}

.hero{left:0;top:183px;width:1200px;height:640px;background:var(--black);overflow:hidden}
.hero-art{position:absolute;left:600px;top:0;width:600px;height:600px;background:radial-gradient(circle at 50% 40%,#1f6fd0 0%,#0a2f6b 35%,#02101f 65%,#000 85%)}
.hero-kicker{left:98px;top:282px;font-size:44px;font-weight:800;color:var(--blue);line-height:50px}
.hero-title{left:98px;top:335px;font-size:45px;font-weight:800;color:var(--white);line-height:53px}
.hero-text{left:98px;top:461px;width:485px;font-size:16.3px;line-height:25px;color:var(--white)}
.btn{background:var(--blue-deep);color:var(--white);font-size:13.5px;font-weight:700;display:flex;align-items:center;justify-content:center;gap:14px;border-radius:3px}
.dots{left:566px;top:725px;display:flex;gap:10px}
.dots i{width:10px;height:10px;border-radius:50%;border:2px solid var(--white);display:block}
.dots i.on{background:var(--blue);border-color:var(--blue)}

.portrait-frame{left:98px;top:878px;width:473px;height:595px;border:4px solid var(--blue)}
.portrait{position:absolute;inset:4px;background:linear-gradient(160deg,#3b3f44 0%,#8a6a4a 55%,#5a4330 100%)}
.eyebrow{font-size:17.5px;color:var(--ink);display:flex;align-items:center;gap:12px}
.eyebrow::after{content:"";width:85px;height:1px;background:#555}
.eyebrow.center::before{content:"";width:85px;height:1px;background:currentColor}
.eyebrow.center::after{background:currentColor}
.about{left:605px;top:873px;width:500px}
.about h1{font-size:44px;font-weight:800;color:var(--blue-deep);margin-top:12px;line-height:52px}
.about h2{font-size:23px;font-weight:400;color:var(--blue)}
.about p{font-size:14.3px;line-height:20.5px;margin-top:12px;color:var(--ink)}
.about h3{font-size:14.5px;font-weight:600;color:var(--blue);margin-top:20px}
.about li{font-size:14.3px;line-height:20.5px}
.about li::before{content:"• "}
.about .url{font-size:14.3px;line-height:20.5px;white-space:nowrap}

.roles{left:0;top:1536px;width:1200px;height:341px;background:linear-gradient(180deg,#1d5ea8,#174f98 60%,#13478f)}
.roles .eyebrow{color:var(--white);justify-content:center;position:absolute;top:48px;width:1200px}
.roles h2{position:absolute;top:78px;width:1200px;text-align:center;color:var(--white);font-size:47px;font-weight:800}
.role{position:absolute;top:170px;height:98px;border-bottom:2px solid #2f7fd3;display:flex;align-items:center;gap:12px}
.role .num{font-size:100px;font-weight:400;color:transparent;-webkit-text-stroke:2px #3b86d6;line-height:90px;width:64px;flex:none}
.role .label{font-size:21px;font-weight:700;color:var(--white);line-height:25px;white-space:nowrap}

.exp-head{left:0;top:1940px;width:1200px}
.exp-head .eyebrow{justify-content:center;color:#222}
.exp-head h2{text-align:center;font-size:48px;font-weight:800;color:var(--blue-deep);margin-top:8px}
.card{top:2100px;width:326px;height:388px;border:2px solid var(--blue);border-radius:10px;box-shadow:0 4px 10px rgba(0,0,0,.15);background:var(--white)}
.card .badge{position:absolute;left:50%;top:-46px;margin-left:-44px;width:88px;height:88px;border-radius:50%;background:var(--blue);display:flex;align-items:center;justify-content:center}
.card h3{margin-top:55px;text-align:center;font-size:17.5px;font-weight:600;color:var(--blue-deep);line-height:25px}
.card ul{margin:18px 20px 0 28px}
.card li{font-size:14.2px;line-height:18px;padding-left:12px;position:relative;color:#222}
.card li::before{content:"•";position:absolute;left:0}

.footer{left:0;top:2600px;width:1200px;height:414px}
.foot-col h4{color:var(--white);font-size:17px;font-weight:700;margin-bottom:16px}
.foot-col a{display:block;color:var(--white);font-size:14px;line-height:24.5px;text-decoration:none}
.foot-col .row{display:flex;gap:12px;color:var(--white);font-size:14px;line-height:17px;margin-bottom:16px}
.divider{width:1px;background:rgba(255,255,255,.5)}
.foot-brand{left:755px;top:2808px;display:flex;align-items:center;gap:12px}
.foot-brand .brand-mark{background:var(--white)}
.foot-brand .brand-name{color:var(--white)}
.copyright{left:0;top:2950px;width:1200px;height:64px;background:var(--navy-dark);color:var(--white);font-size:14.5px;font-weight:500;text-align:center;line-height:64px;letter-spacing:.3px}
</style>
</head>
<body>

<div class="abs brand"><i class="brand-mark"></i><span class="brand-name">Q's &amp; V's</span></div>

<div class="abs contact" style="left:500px">
  <div class="ico"><svg width="20" height="20" viewBox="0 0 24 24" fill="none" stroke="#fff" stroke-width="1.8"><path d="M5 3h4l2 5-3 2a12 12 0 0 0 6 6l2-3 5 2v4a2 2 0 0 1-2 2A17 17 0 0 1 3 5a2 2 0 0 1 2-2z"/></svg></div>
  <div><b>Call us</b><span>(+123) 4410-5577</span></div>
</div>
<div class="abs contact" style="left:699px">
  <div class="ico"><svg width="20" height="16" viewBox="0 0 24 18" fill="none" stroke="#fff" stroke-width="1.8"><rect x="1" y="1" width="22" height="16"/><path d="M1 1l11 9 11-9"/></svg></div>
  <div><b>Mail us</b><span>hello@qvcoaching.example</span></div>
</div>
<div class="abs tools">
  <i class="search"><svg width="14" height="14" viewBox="0 0 24 24" fill="none" stroke="#1a4f94" stroke-width="2.5"><circle cx="10" cy="10" r="7"/><path d="M15 15l7 7"/></svg></i>
  <i></i><i></i><i></i>
</div>

<nav class="abs nav">
  <a class="active" style="left:91px">About Me</a>
  <a style="left:211px">Q's &amp; V's - Agile Team Coaching</a>
  <a style="left:481px">The Team Level</a>
  <a style="left:632px">The Program Level</a>
  <a style="left:805px">Why is Q's &amp; V's here</a>
  <a style="left:995px">Presentations</a>
</nav>

<section class="abs hero">
  <div class="hero-art" role="img" aria-label="Glowing blue coaching dashboard touched by a hand, with goal, trophy, team and conversation symbols"></div>
  <svg class="abs" style="left:0;top:0" width="1200" height="640" viewBox="0 183 1200 640">
    <path d="M0 670 Q600 860 1200 670 L1200 823 L0 823 Z" fill="#fff"/>
    <path d="M0 672 Q600 865 1200 672 Q600 940 0 672 Z" fill="#1a5ba8"/>
  </svg>
</section>
<div class="abs hero-kicker">Q'S AND V'S</div>
<div class="abs hero-title">AGILE IT COACHING<br>AND TRAINING</div>
<p class="abs hero-text">Lorem Ipsum is simply dummy text of the printing and typesetting industry. Lorem Ipsum has been the industry's standard dummy text ever since the 1500s, when an unknown printer took a galley of type and scrambled it to make.</p>
<a class="abs btn" style="left:98px;top:589px;width:152px;height:41px">LEARN MORE <svg width="16" height="16" viewBox="0 0 16 16" fill="none" stroke="#fff" stroke-width="2"><path d="M2 2l6 6-6 6M8 2l6 6-6 6"/></svg></a>
<div class="abs dots"><i class="on"></i><i></i><i></i><i></i></div>

<div class="abs portrait-frame"><div class="portrait" role="img" aria-label="Portrait photo of Joel Brandt in a tan blazer"></div></div>
<section class="abs about">
  <div class="eyebrow">About Me</div>
  <h1>JOEL BRANDT</h1>
  <h2>Senior Scrum Master &amp; Team Agile Coach</h2>
  <p>Joel Brandt is the Owner of Steadfast Project Keys, LLC and serves as Principal Lead Consultant on waterfall and agile contract opportunities. Steadfast Project Keys, LLC has engaged on a contract basis with Summit 300 companies across various industries including banking and credit unions, global supply chain, and international food distribution. Joel Brandt brings 12 years of experience to his clients encompassing various project methodologies including: waterfall, agile, and hybrid frameworks.</p>
  <h3>Coaching Designations</h3>
  <ul>
    <li>CTL-PX</li>
    <li>Certified Sprint Basics Educator</li>
    <li>TCP-ATC</li>
    <li>LIMBr Advanced Scrum Master</li>
    <li>A-CTL</li>
  </ul>
  <h3>Sprint Guild Profile Link</h3>
  <div class="url">https://www.sprintguild.example/community/profile/jbrandt10</div>
  <h3>Badgely Profile Link</h3>
  <div class="url">https://www.badgely.example/users/joel-brandt.b71c3d9e</div>
  <h3>LIMBr Tiered Agile Alliance Profile Link</h3>
  <div class="url">https://community.tieredagile.example/s/profile/0071K0000045gxtRBB</div>
</section>

<section class="abs roles">
  <div class="eyebrow center">What I do</div>
  <h2>ROLES I HAVE HELD</h2>
  <div class="role" style="left:98px;width:206px"><span class="num">1</span><span class="label">Sr.<br>Scrum<br>Master</span></div>
  <div class="role" style="left:325px;width:208px"><span class="num">2</span><span class="label">Advanced<br>LIMBr Scrum<br>Master</span></div>
  <div class="role" style="left:555px;width:250px"><span class="num">3</span><span class="label">Hybrid Scrum<br>Master/ Project<br>Manager</span></div>
  <div class="role" style="left:833px;width:270px"><span class="num">4</span><span class="label">Business Finance<br>Transformation<br>Program Manager</span></div>
</section>

<section class="abs exp-head">
  <div class="eyebrow center">Designation</div>
  <h2>WHAT IS MY EXPERIENCE</h2>
</section>

<div class="abs card" style="left:98px">
  <div class="badge"><svg width="42" height="42" viewBox="0 0 24 24" fill="none" stroke="#fff" stroke-width="1.5"><circle cx="12" cy="9" r="4"/><path d="M4 21c1-4 4-6 8-6s7 2 8 6"/></svg></div>
  <h3>LIMBr Adv Scrum<br>Master</h3>
  <ul>
    <li>Stand up teams</li>
    <li>Run development efforts concurrently leading multiple teams</li>
    <li>Run LIMBr ceremonies</li>
    <li>Scrum of Scrums facilitator</li>
    <li>PI Planning team facilitator (multiple teams on ART)</li>
    <li>Teach and coach to advanced development team strategies</li>
    <li>Lead program level communications and business status updates on behalf of the team</li>
  </ul>
</div>
<div class="abs card" style="left:437px">
  <div class="badge"><svg width="42" height="42" viewBox="0 0 24 24" fill="none" stroke="#fff" stroke-width="1.5"><circle cx="8" cy="8" r="3"/><circle cx="16" cy="8" r="3"/><path d="M2 19c1-3 3-5 6-5s5 2 6 5M12 19c1-3 2-5 4-5s4 2 5 5"/></svg></div>
  <h3>Hybrid Scrum Master /<br>Project Manger</h3>
  <ul>
    <li>Standup teams</li>
    <li>Run multiple program level projects simultaneously</li>
    <li>Implement custom hybrid development strategies</li>
    <li>Manage to project triple constraints</li>
    <li>Communications lead and business liaison</li>
    <li>Use multiple coaching styles based on team and project</li>
  </ul>
</div>
<div class="abs card" style="left:776px">
  <div class="badge"><svg width="42" height="42" viewBox="0 0 24 24" fill="none" stroke="#fff" stroke-width="1.5"><rect x="3" y="4" width="18" height="13"/><path d="M9 21h6M12 17v4M10 9l-2 2 2 2M14 9l2 2-2 2"/></svg></div>
  <h3>Business Transformation<br>Program Manager</h3>
  <ul>
    <li>Lead business transformation efforts at the program level</li>
    <li>Work with multiple product owners, business analysts, and business stakeholders on requirements</li>
    <li>Lead the international rollout, onboarding, and support of new transformational CRM tool, PipeCRM</li>
    <li>Standup and lead multi-functional teams consisting of business and technology team members</li>
    <li>Serve as program organization and communications lead</li>
  </ul>
</div>

<a class="abs btn" style="left:422px;top:2525px;width:357px;height:42px">WHERE DOES COACHING COME IN TO PLAY <svg width="16" height="16" viewBox="0 0 16 16" fill="none" stroke="#fff" stroke-width="2"><path d="M2 2l6 6-6 6M8 2l6 6-6 6"/></svg></a>

<svg class="abs footer" width="1200" height="414" viewBox="0 0 1200 414">
  <defs>
    <linearGradient id="footBg" x1="0" y1="0" x2="0" y2="1">
      <stop offset="0" stop-color="#134a92"/><stop offset="1" stop-color="#0f3c7d"/>
    </linearGradient>
  </defs>
  <path d="M0 140 Q600 -70 1200 140 L1200 414 L0 414 Z" fill="#1a72bf"/>
  <path d="M0 148 Q600 -30 1200 148 L1200 414 L0 414 Z" fill="url(#footBg)"/>
</svg>
<div class="abs foot-col" style="left:125px;top:2730px">
  <h4>QUICK LINKS</h4>
  <a>About Me</a>
  <a>Q's &amp; V's - Agile Team Coaching</a>
  <a>The Team Level</a>
  <a>The Program Level</a>
  <a>Why is Q's &amp; V's here</a>
  <a>Presentations</a>
</div>
<div class="abs divider" style="left:390px;top:2732px;height:190px"></div>
<div class="abs foot-col" style="left:457px;top:2730px;width:250px">
  <h4>CONTACT US</h4>
  <div class="row"><svg width="10" height="14" viewBox="0 0 10 14" fill="#fff"><path d="M5 0a5 5 0 0 0-5 5c0 4 5 9 5 9s5-5 5-9a5 5 0 0 0-5-5zm0 7a2 2 0 1 1 0-4 2 2 0 0 1 0 4z"/></svg><span>Unit 52, Ground Floor, Birch Court,<br>Eastfield Office Park<br>88 Sample Services Road<br>Elmhurst Vale</span></div>
  <div class="row"><svg width="10" height="10" viewBox="0 0 24 18" fill="none" stroke="#fff" stroke-width="3"><rect x="1" y="1" width="22" height="16"/><path d="M1 1l11 9 11-9"/></svg><span>hello@qvcoaching.example</span></div>
  <div class="row"><svg width="10" height="10" viewBox="0 0 24 24" fill="none" stroke="#fff" stroke-width="3"><path d="M5 3h4l2 5-3 2a12 12 0 0 0 6 6l2-3 5 2v4a2 2 0 0 1-2 2A17 17 0 0 1 3 5a2 2 0 0 1 2-2z"/></svg><span>(+123) 4410-5577</span></div>
</div>
<div class="abs divider" style="left:728px;top:2732px;height:190px"></div>
<div class="abs foot-brand"><i class="brand-mark"></i><span class="brand-name">Q's &amp; V's</span></div>

<div class="abs copyright">© 2022 Q'S AND V'S - AGILE IT COACHING AND TRAINING. - ALL RIGHTS RESERVED</div>

</body>
</html>
```